Velmoria-Quillmesh Partial Redesign - Web App

Are you able to apply your creativity to an existing layout? I’m convinced that even just a few touches can make a big difference to add personality and professionalism to a website design, and I’m looking for someone able to use existing ideas and bring them to the next level while keeping inside some given constraints.
The actual job is to improve an existing design concept and to apply it creatively to a landing page, a simple home page, and an older web app (single page website).
To help you start with a clear picture of the current situation and of my requirements, I created a detailed brief with screenshots, live examples, and complete instructions. You can find it attached to this job.
My tastes are inclined towards clean and simple designs. For this project I'm not looking for dazzling novelty, but for very solid craftsmanship. Are the right man - or woman - for the job?
Updates
I wanted to thank everybody who participated in this project. I made a choice, but also other designs were interesting. Hope to work with you another time.
Target Market(s)
Our main target is social media marketers and startuppers
Look and feel
Each slider illustrates characteristics of the customer's brand and the style your logo design should communicate.

```html
<!DOCTYPE html>
<html lang="en">
<head>
<meta charset="utf-8">
<title>Velmoria – Hashtag Summary</title>
<link rel="stylesheet" href="https://fonts.googleapis.com/css2?family=Noto+Sans:ital,wght@0,400;0,700;1,400;1,700&display=swap">
<style>
  :root {
    --dark: #222222;
    --blue: #0a6fd1;
    --blue-dark: #0656a8;
    --text: #555555;
    --text-dark: #444444;
    --red: #dc3912;
    --pie-blue: #3366cc;
    --orange: #ff9900;
    --green: #109618;
    --hub: #4285f4;
  }
  * { box-sizing: border-box; margin: 0; padding: 0; }
  html, body { width: 800px; height: 1200px; overflow: hidden; }
  body { position: relative; background: #fff; font-family: "Noto Sans", sans-serif; color: var(--text); }
  .abs { position: absolute; }

  .site-header { position: absolute; left: 0; top: 0; width: 800px; height: 94px; background: linear-gradient(#262626, #1c1c1c); }
  .brand { position: absolute; left: 77px; top: 30px; display: flex; align-items: center; gap: 10px; }
  .brand-mark { width: 22px; height: 22px; background: #8a8a8a; }
  .brand-name { color: #bdbdbd; font-size: 26px; font-weight: 700; line-height: 1; }
  .brand-tag { position: absolute; left: 110px; top: 61px; color: #a8a8a8; font-size: 9.5px; white-space: nowrap; }
  .nav { position: absolute; top: 44px; height: 19px; display: flex; align-items: center; justify-content: center; font-size: 7.5px; font-weight: 700; color: #fff; border-radius: 2px; background: linear-gradient(#444, #2e2e2e); border: 1px solid #555; }
  .nav.active { background: linear-gradient(#1580e0, var(--blue-dark)); border-color: #0a4f98; }
  .nav-sep { position: absolute; top: 43px; width: 1px; height: 21px; background: #555; }

  .hero { position: absolute; left: 0; top: 94px; width: 800px; height: 117px; background: linear-gradient(#fff, #ececec); border-bottom: 1px solid #bdbdbd; }
  .hero-title { position: absolute; left: 77px; top: 124px; font-size: 20px; font-weight: 700; color: #555; }
  .hero-title span { color: var(--blue); }
  .hero-sub { position: absolute; left: 77px; top: 150px; font-size: 10.5px; font-style: italic; color: var(--blue); }
  .hero-sub b { font-weight: 700; }

  .tab { position: absolute; top: 200px; height: 22px; display: flex; align-items: center; justify-content: center; font-size: 9.5px; font-weight: 700; color: var(--blue-dark); background: linear-gradient(#fafafa, #dedede); border: 1px solid #bbb; box-shadow: 0 1px 2px rgba(0,0,0,.25); }
  .tab.active { color: #fff; background: linear-gradient(#1580e0, var(--blue-dark)); border-color: #0a4f98; }

  .stat { position: absolute; top: 266px; width: 122px; height: 57px; transform: skewX(-8deg); border-radius: 3px; background: linear-gradient(#f4f4f4, #d9d9d9); box-shadow: 0 1px 2px rgba(0,0,0,.2); }
  .stat.blue { background: linear-gradient(#1f8be6, var(--blue-dark)); }
  .stat-in { transform: skewX(8deg); text-align: center; padding-top: 9px; }
  .stat-num { font-size: 18px; font-weight: 700; color: #666; line-height: 1.1; }
  .stat-label { font-size: 8.5px; font-weight: 700; color: #666; margin-top: 4px; }
  .stat.blue .stat-num, .stat.blue .stat-label { color: #fff; }

  .divider { position: absolute; left: 0; width: 800px; height: 3px; background: linear-gradient(#d2d2d2, #f2f2f2); }
  .section-title { position: absolute; left: 0; width: 800px; text-align: center; font-size: 18px; font-weight: 700; color: var(--text-dark); text-decoration: underline; text-underline-offset: 3px; }
  .chart-title { position: absolute; font-size: 11px; color: #444; letter-spacing: .3px; display: flex; align-items: center; gap: 4px; white-space: nowrap; }
  .pip { display: inline-block; width: 4px; height: 15px; border-radius: 2px; margin-left: 3px; }
  .pip.red { background: var(--red); }
  .pip.blue { background: var(--hub); }

  .legend { position: absolute; font-size: 8px; color: #222; line-height: 1.35; }
  .legend-row { display: flex; gap: 4px; align-items: flex-start; margin-bottom: 2px; }
  .swatch { width: 9px; height: 9px; margin-top: 1px; flex: none; }

  .site-footer { position: absolute; left: 0; top: 1105px; width: 800px; height: 95px; background: linear-gradient(#262626, #1c1c1c); }
  .foot-brand { position: absolute; left: 92px; top: 1143px; display: flex; align-items: center; gap: 8px; }
  .foot-brand .brand-mark { width: 16px; height: 16px; }
  .foot-brand .brand-name { font-size: 19px; }
  .foot-tag { position: absolute; left: 116px; top: 1164px; font-size: 6.5px; color: #999; white-space: nowrap; }
  .foot-copy { position: absolute; left: 273px; top: 1146px; font-size: 7.5px; color: #aaa; line-height: 1.6; }
  .foot-addr { position: absolute; left: 450px; top: 1148px; font-size: 7.5px; color: #aaa; line-height: 1.5; }
  .social { position: absolute; top: 1146px; width: 17px; height: 17px; border-radius: 3px; }
</style>
</head>
<body>
  <header class="site-header"></header>
  <div class="brand"><span class="brand-mark"></span><span class="brand-name">Velmoria</span></div>
  <div class="brand-tag">Social Signal Insight Platform</div>
  <div class="nav active" style="left:529px;width:61px">Products ▾</div>
  <div class="nav-sep" style="left:595px"></div>
  <div class="nav" style="left:600px;width:36px">Blog</div>
  <div class="nav" style="left:641px;width:38px">About</div>
  <div class="nav-sep" style="left:684px"></div>
  <div class="nav" style="left:691px;width:32px">
    <svg width="14" height="10" viewBox="0 0 14 10"><circle cx="5" cy="3" r="2.5" fill="#fff"/><path d="M0 10 Q5 4 10 10Z" fill="#fff"/><path d="M11 4 L14 4 L12.5 6Z" fill="#fff"/></svg>
  </div>

  <section class="hero"></section>
  <h1 class="hero-title">Hashtag: <span>#socialtips</span></h1>
  <p class="hero-sub"><b>Tracked influencers:</b> @dariovenn, @lunaorbisme</p>

  <nav>
    <div class="tab active" style="left:236px;width:74px">Summary</div>
    <div class="tab" style="left:322px;width:73px">Timeline</div>
    <div class="tab" style="left:406px;width:74px">Influencers</div>
    <div class="tab" style="left:490px;width:73px">Hashtags</div>
  </nav>

  <div class="stat" style="left:82px"><div class="stat-in"><div class="stat-num">8</div><div class="stat-label">Observed Days</div></div></div>
  <div class="stat blue" style="left:210px"><div class="stat-in"><div class="stat-num">8,234,567</div><div class="stat-label">Total Impressions</div></div></div>
  <div class="stat blue" style="left:338px"><div class="stat-in"><div class="stat-num">840</div><div class="stat-label">Total Tweets</div></div></div>
  <div class="stat" style="left:466px"><div class="stat-in"><div class="stat-num">1,076,658</div><div class="stat-label">Daily Impressions</div></div></div>
  <div class="stat" style="left:594px"><div class="stat-in"><div class="stat-num">145</div><div class="stat-label">Daily Tweets</div></div></div>

  <div class="divider" style="top:366px"></div>
  <h2 class="section-title" style="top:397px">TREND ANALYSIS</h2>

  <div class="chart-title" style="left:121px;top:471px">Trend With Your Influencers <span class="pip red"></span><span class="pip red"></span><span class="pip blue"></span></div>
  <div class="chart-title" style="left:470px;top:471px">Trend Without Your Influencers <span class="pip red"></span><span class="pip red"></span></div>

  <svg class="abs" style="left:123px;top:510px" width="200" height="200" viewBox="-100 -100 200 200" role="img" aria-label="Trend gauge with influencers, value 3">
    <circle r="100" fill="#c8c8c8"/><circle r="93" fill="#f5f5f5" stroke="#bbb"/>
    <path d="M -55.86 55.86 A 79 79 0 0 1 -58.01 -53.63" fill="none" stroke="var(--red)" stroke-width="15"/>
    <path d="M -58.01 -53.63 A 79 79 0 0 1 58.01 -53.63" fill="none" stroke="var(--orange)" stroke-width="15"/>
    <path d="M 58.01 -53.63 A 79 79 0 0 1 55.86 55.86" fill="none" stroke="var(--green)" stroke-width="15"/>
    <text x="0" y="-20" text-anchor="middle" font-size="22" fill="#333">Trend</text>
    <text x="-33" y="48" text-anchor="middle" font-size="12" fill="#444">-100</text>
    <text x="35" y="48" text-anchor="middle" font-size="12" fill="#444">100</text>
    <text x="0" y="77" text-anchor="middle" font-size="20" fill="#111">3</text>
    <polygon points="5.6,-80 3,0 1,28 -3,0" fill="#e0674c" stroke="#c04a30" stroke-width=".8"/>
    <circle r="13" fill="var(--hub)"/>
  </svg>
  <svg class="abs" style="left:473px;top:510px" width="200" height="200" viewBox="-100 -100 200 200" role="img" aria-label="Trend gauge without influencers, value 3">
    <circle r="100" fill="#c8c8c8"/><circle r="93" fill="#f5f5f5" stroke="#bbb"/>
    <path d="M -55.86 55.86 A 79 79 0 0 1 -58.01 -53.63" fill="none" stroke="var(--red)" stroke-width="15"/>
    <path d="M -58.01 -53.63 A 79 79 0 0 1 58.01 -53.63" fill="none" stroke="var(--orange)" stroke-width="15"/>
    <path d="M 58.01 -53.63 A 79 79 0 0 1 55.86 55.86" fill="none" stroke="var(--green)" stroke-width="15"/>
    <text x="0" y="-20" text-anchor="middle" font-size="22" fill="#333">Trend</text>
    <text x="-33" y="48" text-anchor="middle" font-size="12" fill="#444">-100</text>
    <text x="35" y="48" text-anchor="middle" font-size="12" fill="#444">100</text>
    <text x="0" y="77" text-anchor="middle" font-size="20" fill="#111">3</text>
    <polygon points="5.6,-80 3,0 1,28 -3,0" fill="#e0674c" stroke="#c04a30" stroke-width=".8"/>
    <circle r="13" fill="var(--hub)"/>
  </svg>

  <div class="divider" style="top:751px"></div>
  <h2 class="section-title" style="top:789px">YOUR INFLUENCERS ANALYSIS</h2>

  <div class="chart-title" style="left:77px;top:862px">Your Influencers <span class="pip blue"></span> vs Rest Of The Internet <span class="pip red"></span><span class="pip red"></span></div>
  <div class="chart-title" style="left:445px;top:862px">Your Influencers <span class="pip blue"></span> vs Your Influencers <span class="pip blue"></span></div>

  <svg class="abs" style="left:146px;top:907px" width="132" height="132" viewBox="-66 -66 132 132" role="img" aria-label="Pie chart: tracked influencers 14.9%, others 85.1%">
    <path d="M0 0 L0 -64 A64 64 0 0 1 51.5 -38 Z" fill="var(--pie-blue)" stroke="#fff" stroke-width="1"/>
    <path d="M0 0 L51.5 -38 A64 64 0 1 1 0 -64 Z" fill="var(--red)" stroke="#fff" stroke-width="1"/>
    <text x="20" y="-38" text-anchor="middle" font-size="7.5" fill="#fff">14.9%</text>
    <text x="-22" y="42" text-anchor="middle" font-size="7.5" fill="#fff">85.1%</text>
  </svg>
  <div class="legend" style="left:289px;top:903px">
    <div class="legend-row"><span class="swatch" style="background:var(--pie-blue)"></span><span>Tracked<br>Influencers</span></div>
    <div class="legend-row"><span class="swatch" style="background:var(--red)"></span><span>Others</span></div>
  </div>

  <svg class="abs" style="left:495px;top:907px" width="132" height="132" viewBox="-66 -66 132 132" role="img" aria-label="Pie chart: first influencer 8.1%, second influencer 91.9%">
    <path d="M0 0 L0 -64 A64 64 0 0 1 31.2 -55.9 Z" fill="var(--pie-blue)" stroke="#fff" stroke-width="1"/>
    <path d="M0 0 L31.2 -55.9 A64 64 0 1 1 0 -64 Z" fill="var(--red)" stroke="#fff" stroke-width="1"/>
    <text x="12" y="-45" text-anchor="middle" font-size="7.5" fill="#fff">8.1%</text>
    <text x="-13" y="48" text-anchor="middle" font-size="7.5" fill="#fff">91.9%</text>
  </svg>
  <div class="legend" style="left:638px;top:903px">
    <div class="legend-row"><span class="swatch" style="background:var(--pie-blue)"></span><span>corvinhale...</span></div>
    <div class="legend-row"><span class="swatch" style="background:var(--red)"></span><span>mirabelos</span></div>
  </div>

  <footer class="site-footer"></footer>
  <div class="foot-brand"><span class="brand-mark"></span><span class="brand-name">Velmoria</span></div>
  <div class="foot-tag">Social Signal Insight Platform</div>
  <div class="foot-copy">Copyright © 2012. All Rights Reserved.<br>Privacy Policy &nbsp;|&nbsp; Terms of Use</div>
  <div class="foot-addr">48 Larch Lane<br>K9 4TR Brenmoor, UK</div>
  <div class="social" style="left:603px;background:#4fb3e8"></div>
  <div class="social" style="left:624px;background:#3b5b9a"></div>
  <div class="social" style="left:645px;background:#c4302b"></div>
  <div class="social" style="left:666px;background:#f08a24"></div>
</body>
</html>
```